Velmoria-Quillmesh Partial Redesign - Web App

Are you able to apply your creativity to an existing layout? I’m convinced that even just a few touches can make a big difference to add personality and professionalism to a website design, and I’m looking for someone able to use existing ideas and bring them to the next level while keeping inside some given constraints.
The actual job is to improve an existing design concept and to apply it creatively to a landing page, a simple home page, and an older web app (single page website).
To help you start with a clear picture of the current situation and of my requirements, I created a detailed brief with screenshots, live examples, and complete instructions. You can find it attached to this job.
My tastes are inclined towards clean and simple designs. For this project I'm not looking for dazzling novelty, but for very solid craftsmanship. Are the right man - or woman - for the job?
Updates
I wanted to thank everybody who participated in this project. I made a choice, but also other designs were interesting. Hope to work with you another time.
Target Market(s)
Our main target is social media marketers and startuppers
Look and feel
Each slider illustrates characteristics of the customer's brand and the style your logo design should communicate.

```html
<!DOCTYPE html>
<html lang="en">
<head>
<meta charset="utf-8">
<title>Velmoria – Social Signal Brand Insight Suite</title>
<link href="https://fonts.googleapis.com/css2?family=Source+Sans+3:wght@400;600;700&display=swap" rel="stylesheet">
<style>
:root{
  --ink:#2e2f33;
  --dark:#3c3e44;
  --dark-2:#4b4d53;
  --red:#d80f0f;
  --red-hi:#f2372b;
  --grey:#c6c6c6;
  --rule:#c9c9c9;
  --muted:#6b6b6b;
  --pale:#f3f3f3;
  --sky:#b8e6f7;
  --sky-ink:#1d6f8e;
  --white:#ffffff;
}
*{box-sizing:border-box;margin:0;padding:0}
html,body{width:1200px;height:1134px;overflow:hidden}
body{font-family:"Source Sans 3",Arial,sans-serif;color:var(--ink);background:var(--white);position:relative}
.abs{position:absolute}
.top-strip{left:0;top:0;width:1200px;height:6px;background:var(--dark)}
.header{left:0;top:6px;width:1200px;height:127px;background:linear-gradient(#ececec,#fafafa)}
.tab{top:6px;height:27px;background:var(--dark-2);color:#eee;font-size:15px;line-height:25px;text-align:center;border-radius:0 0 6px 6px}
.brand{left:128px;top:40px;display:flex;align-items:center;gap:20px}
.brand-mark{width:140px;height:82px;border-radius:50%;background:#dcdcdc}
.brand-name{font-size:46px;font-weight:700;color:#43454b;line-height:1}
.brand-tag{font-size:16px;color:#43454b;margin-left:14px;margin-top:2px}
.nav{left:676px;top:65px;width:399px;height:36px;background:var(--dark-2);border-radius:8px;display:flex;align-items:center;padding-left:8px}
.nav a{color:#f0f0f0;text-decoration:none;font-size:15px;padding:0 10px;border-right:1px solid #5e6066;line-height:26px}
.nav a:last-child{border:none}
.nav-pointer{left:700px;top:100px;width:0;height:0;border:7px solid transparent;border-top-color:var(--dark-2)}
.band{left:0;top:133px;width:1200px;height:89px;background:linear-gradient(#3a3c42,#4d4f55)}
.band-split{left:597px;top:145px;width:2px;height:75px;background:#2f3035}
.search-box{left:140px;top:165px;width:297px;height:34px;background:linear-gradient(#fff,#e6e6e6);border-radius:8px;display:flex;align-items:center;padding-left:12px;color:#aaa;font-size:13px}
.search-box .lens{width:16px;height:16px;border:2px solid #9a9a9a;border-radius:50%;margin-right:14px}
.search-box .sep{width:1px;height:18px;background:#ccc;margin-right:8px}
.btn-red{background:linear-gradient(var(--red-hi),var(--red));color:#fff;font-weight:600;border-radius:6px;text-align:center}
.search-btn{left:448px;top:164px;width:109px;height:34px;font-size:18px;line-height:34px}
.counter-label{left:641px;top:170px;color:#fff;font-weight:700;font-size:18px}
.digit{top:156px;height:42px;background:#2f3035;color:#fff;font-weight:700;font-size:31px;line-height:42px;text-align:center;border-radius:6px}
.comma{top:152px;color:#fff;font-weight:700;font-size:30px;line-height:42px}
.counter-sub{left:872px;top:200px;color:#eee;font-size:13px}
.variants{left:129px;top:249px;width:610px;font-size:18px;line-height:30px;font-weight:600}
.variants .k{color:var(--ink)}
.variants .v{color:var(--red)}
.graph{left:0;top:330px}
.graph text{font-family:"Source Sans 3",Arial,sans-serif;font-size:17px;fill:#222;text-anchor:middle}
.mode{top:776px;height:34px;font-size:17px;line-height:34px;text-align:center;border-radius:7px;color:#fff;font-weight:600}
.mode-simple{left:405px;width:131px}
.mode-adv{left:546px;width:161px;background:var(--dark-2)}
.divider{left:744px;top:255px;width:1px;height:672px;background:var(--rule)}
.side-title{color:var(--red);font-weight:700;font-size:18px}
.follow-dot{left:905px;top:232px;width:42px;height:32px;border-radius:50%;background:#35373c}
.tweet{left:783px;width:292px;height:76px}
.avatar{left:0;top:0;width:64px;height:56px;border:3px solid #c8c8c8;background:linear-gradient(#6b5147,#2f241f)}
.tweet p{position:absolute;left:84px;top:-6px;width:208px;font-size:11px;line-height:14.5px;text-align:justify}
.stamp{position:absolute;left:84px;top:45px;display:flex;align-items:center;gap:6px}
.stamp .dot{width:20px;height:14px;border-radius:50%;background:#3ab3e6}
.stamp span{background:var(--sky);color:var(--sky-ink);font-size:11px;padding:2px 7px;border-radius:9px}
.influencers{left:782px;top:684px;width:283px;list-style:none}
.influencers li{height:36px;border-bottom:1px dashed var(--rule);font-size:14px;line-height:36px;padding-left:14px;position:relative;color:#444}
.influencers li::before{content:"";position:absolute;left:0;top:14px;border:4px solid transparent;border-left:6px solid var(--red);border-right:0}
.influencers li.lead{color:var(--red)}
.followers{position:absolute;left:90px;top:6px;height:24px;line-height:24px;background:#e2e2e2;color:#444;padding:0 9px;border-radius:7px;font-size:14px}
.footer{left:0;top:937px;width:1200px;height:197px;background:linear-gradient(#3c3e44,#4a4c52);color:#fff}
.foot-title{top:15px;font-size:20px;font-weight:600}
.foot-links{top:51px;list-style:none;font-size:15px;line-height:30px}
.social{left:421px;top:56px;display:flex;gap:6px}
.social i{width:28px;height:28px;border-radius:50%;background:#6c6e74;display:block}
.social-names{left:421px;top:99px;font-size:13px}
.foot-brand{left:645px;top:38px;display:flex;align-items:center;gap:16px;opacity:.35}
.foot-brand .brand-mark{width:128px;height:78px;background:#6a6c72}
.foot-brand .brand-name{color:#9a9ca2;font-size:44px}
.foot-brand .brand-tag{color:#9a9ca2;font-size:15px}
.legal{right:178px;top:152px;font-size:12px;text-align:right;line-height:21px}
</style>
</head>
<body>
<div class="abs top-strip"></div>
<header class="abs header"></header>
<div class="abs tab" style="left:884px;width:111px">Admin Login</div>
<div class="abs tab" style="left:1006px;width:69px">Login</div>

<div class="abs brand">
  <div class="brand-mark"></div>
  <div>
    <div class="brand-name">Velmoria</div>
    <div class="brand-tag">Social Signal Brand Insight Suite</div>
  </div>
</div>

<nav class="abs nav">
  <a href="#">Home</a><a href="#">About</a><a href="#">Blog</a><a href="#">Top influencers</a><a href="#">Top Variants</a>
</nav>
<div class="abs nav-pointer"></div>

<section class="abs band"></section>
<div class="abs band-split"></div>
<div class="abs search-box"><span class="lens"></span><span class="sep"></span>Search</div>
<div class="abs btn-red search-btn">Search</div>
<div class="abs counter-label">HASHTAGS FOUND SO FAR:</div>
<div class="abs digit" style="left:867px;width:54px">00</div>
<div class="abs comma" style="left:924px">,</div>
<div class="abs digit" style="left:933px;width:65px">022</div>
<div class="abs comma" style="left:1000px">,</div>
<div class="abs digit" style="left:1010px;width:65px">158</div>
<div class="abs counter-sub">in 567,419,411 tweets</div>

<div class="abs variants"><span class="k">Variants: </span><span class="v">hashtag:84% Hashtag:10% HASHTAG:3% HashTag:3% hashTag:0% HASHtag:0% Popularity: 65.8</span></div>

<svg class="abs graph" width="740" height="440" viewBox="0 330 740 440" role="img" aria-label="Related word network for the hashtag">
  <g stroke="#555" stroke-width="2.5">
    <line x1="430" y1="570" x2="262" y2="425"/>
    <line x1="430" y1="570" x2="403" y2="465"/>
    <line x1="430" y1="570" x2="505" y2="515"/>
    <line x1="430" y1="570" x2="300" y2="530"/>
    <line x1="430" y1="570" x2="210" y2="598"/>
    <line x1="430" y1="570" x2="350" y2="630"/>
    <line x1="430" y1="570" x2="420" y2="665"/>
    <line x1="430" y1="570" x2="510" y2="615"/>
  </g>
  <g fill="var(--grey)">
    <polygon points="242,366 274,385 262,430 222,432 210,392"/>
    <polygon points="398,350 462,385 452,473 372,475 337,400"/>
    <polygon points="500,453 550,445 577,490 545,535 485,510"/>
    <polygon points="232,483 290,470 323,535 287,572 225,555"/>
    <polygon points="158,600 180,572 220,580 222,622 175,633"/>
    <polygon points="290,630 330,598 368,625 355,670 310,677"/>
    <polygon points="383,705 390,665 458,658 475,710 430,748"/>
    <polygon points="484,625 540,572 608,602 600,680 520,695"/>
  </g>
  <polygon points="485,570 447,625 383,602 378,538 447,516" fill="var(--red)"/>
  <text x="242" y="408">a</text>
  <text x="400" y="423">you</text>
  <text x="531" y="494">to</text>
  <text x="274" y="527">everything</text>
  <text x="192" y="609">every</text>
  <text x="328" y="648">when</text>
  <text x="428" y="705">que</text>
  <text x="546" y="644">People</text>
  <text x="424" y="575" style="fill:#fff">Hastag</text>
</svg>

<div class="abs mode mode-simple btn-red">SIMPLE MODE</div>
<div class="abs mode mode-adv">ADVANCED MODE</div>

<div class="abs divider"></div>

<div class="abs side-title" style="left:779px;top:250px">FOLLOW ME ON</div>
<div class="abs follow-dot"></div>

<div class="abs tweet" style="top:300px">
  <div class="abs avatar" role="img" aria-label="Profile photo of the tweet author"></div>
  <p>MiraQuell_: RT @talkTeoRa: #People #Who #Have #Too #Hashtag #Everything #On #Snapgram like chill dude.</p>
  <div class="stamp"><i class="dot"></i><span>22 seconds ago</span></div>
</div>
<div class="abs tweet" style="top:382px">
  <div class="abs avatar" style="background:linear-gradient(#c9a184,#8a5a3e)" role="img" aria-label="Profile photo of the tweet author"></div>
  <p>MiraQuell_: RT @talkTeoRa: #People #Who #Have #Too #Hashtag #Everything #On #Snapgram like chill dude.</p>
  <div class="stamp"><i class="dot"></i><span>22 seconds ago</span></div>
</div>
<div class="abs tweet" style="top:469px">
  <div class="abs avatar" role="img" aria-label="Profile photo of the tweet author"></div>
  <p>MiraQuell_: RT @talkTeoRa: #People #Who #Have #Too #Hashtag #Everything #On #Snapgram like chill dude.</p>
  <div class="stamp"><i class="dot"></i><span>22 seconds ago</span></div>
</div>
<div class="abs tweet" style="top:551px">
  <div class="abs avatar" style="background:linear-gradient(#c9a184,#8a5a3e)" role="img" aria-label="Profile photo of the tweet author"></div>
  <p>MiraQuell_: RT @talkTeoRa: #People #Who #Have #Too #Hashtag #Everything #On #Snapgram like chill dude.</p>
  <div class="stamp"><i class="dot"></i><span>22 seconds ago</span></div>
</div>

<div class="abs side-title" style="left:779px;top:651px">THE TOP 6&nbsp; INFLUENCERS FOR #TAG</div>
<ul class="abs influencers">
  <li class="lead">dvlorenzo<span class="followers">9,628,704 followers</span></li>
  <li>adamkestrel</li>
  <li>JoeyMarsh_</li>
  <li>rainwhitby</li>
  <li>MilaCorran</li>
  <li>RayTQ</li>
</ul>

<footer class="abs footer">
  <div class="abs foot-title" style="left:150px">QUICK LINKS</div>
  <ul class="abs foot-links" style="left:153px"><li>Home</li><li>About</li><li>Blog</li><li>Summary</li></ul>
  <ul class="abs foot-links" style="left:295px"><li>Timeline</li><li>Influencers</li><li>Hashtags</li><li>Contact Us</li></ul>
  <div class="abs foot-title" style="left:421px">FOLLOW US ON</div>
  <div class="abs social"><i></i><i></i><i></i><i></i></div>
  <div class="abs social-names">chirper | friendbook | plusline | linkup</div>
  <div class="abs foot-brand"><div class="brand-mark"></div><div><div class="brand-name">Velmoria</div><div class="brand-tag">Social Signal Brand Insight Suite</div></div></div>
  <div class="abs legal">Terms &amp; Conditions | Privacy Policy<br>© 2012.www.velmoria.com</div>
</footer>
</body>
</html>
```